Mobile Repair Service on location needs a Web Design

We are starting a new mobile device repair service called Handset Haven and our website needs a design!

Hello Designers!
First, we'd like to make clear this is more than a simple web design contest, we want the designers to create an idea. We want someone who can create the whole theme of the service's we provide. We want someone that can help design our visual branding, help us communicate a sentiment. And we are willing to pay for that.

Who are we?
Our company is based in Rotterdam, the Netherlands. We provide different services for all kinds of electronic devices. The kind of services we provide are, among other things, installations of hardware and software and the repair of broken or malfunctioning devices.
We are starting a new service that offers mobile device repairs on location, be it at the home of our customers, their office, or any other place. Just give us the address and we will come to you for the repair job. This is also our main USP. We have multiple skilled engineers who drive trough the country on a daily basis and can be on location within a working day. Repair is done immediately onsite while the customer waits. At this stage we will start with the smartphone product-group within the mobile devices. In a second phase we might also add tablets.
People don't want to be without their phone for weeks because of some parts that needed to be ordered by a repair center they had to sent their phone to. We offer a fully functional mobile repair center in the form of specially customized vans. These vans have all the tools and utilities needed by our engineers to safely repair your mobile device. Your phone is being repaired directly in front of you, the next business-day, on a location you desire.

For this new service we are creating a website called Handset Haven. The website needs a story and matching design and this is where you come in. We are not looking for a simple template design we can get from any place. We need a story. We want you to create an idea, build a unique theme or vision that helps sell the product/service. This goes beyond the design of the website. We need the whole package, the design you are creating needs to have returning elements like icons, color use, images, maybe even characters etc. You name it! There needs to be a common thread in the design so we can reuse elements in, for example, the email templates, the work order or receipt we give to our customers (we may contact the winner of the contest to design these for us as well!).

The name 'Handset Haven' is chosen. Rehab (short for rehabilitate) has a bold and playful tone to it and the design needs to reflect the name. So we're looking for a somewhat playful and cheeky design. Definitely not too serious and definitely modern. We already got a logo that we love and that fit's this description (see attached design documents for the logo). It's bold, powerful and fun. Our web design needs to reflect this as well and has to fit in with our logo.
We would really like it if the design somehow incorporates elements that highlight our unique selling points (repairs on location, we come to you etc.). We would really like some form of story telling in the design. Think clumsy people breaking their phones. Teenagers in tears because they have no access to their friends. People nowadays have the need to always be 'connected'. What happens when your phone is broken or malfunctioning? We're handling tech, we are nerds and a little bit weird, but we're professionals and here to help you with your problem. The sentiment Byte Brigade tries to communicate is something we really like. We're looking for fresh idea's, anything goes!

In an overview all Unique Selling Points of the Handset haven service:
- Professional service on location. Don’t ship to us we will come to you!
- Clear pricing upfront. No hidden cost.
- Next business-day repair.
- Backed by a professional call center open 12 hours a day and open on a Saturday as well
- Backed by a professional repair center with more then 12 years of experience
- Repair is done by certified engineers
- 1 year warranty on the repair

The process:
The main function of our website will be for customers to make a repair request. A customer will visit our website and can make a repair request immediately by going through a 'request-order-flow'. In this flow he or she will need to fill in some forms and can select wich type/model/brand of mobile device he or she has and what parts need to be repaired. After a request is placed we will call the customer back (within an hour) for a short intake and to set a date/time and location. Our engineer will meet the customer at the specified location and will repair the device onsite in one of our mobile repair centers, which is a specialized van equipped with all the tools needed for device restorations.
So in short the steps are:
- Choose your device and repair job
- Place the order
- Get a callback within the hour
- Set date and location
- We will come to you.

Website functionality:
Our website is our main form of communication. So the sentiment we want to communicate needs be reflected in the design. We need a main/front page designed (preferably a long scrolling page design) containing:
1. Customers will be able to request a repair job directly on our website. So there will need to be a prominent button/link at the top of our main page that will bring the customer to this 'request-order-flow'. This is the main flow which needs to be full focus on the front page. All other items are secondary.
2. The general information of who we are and what we do, and why the customer should choose us. Preferably in short bullet-point type keywords/sentences with icons or other visual cues. See our unique selling points to get an idea of the information that will be displayed here.
3. There needs to be a section that will explain the process (see above) of a repair request step-by- step, again in brief short key sentences and with (custom) icons.
4. There needs to be a section that explains to the customer he/she can always contact us if they are not sure what the problem is with their device, and for this reason are not sure what repair request they should order.
5. We want to implement some functionality that display customer ratings or customer reviews. So there needs to be room for some kind of widget of plugin we're going to implement which shows these reviews.
6. A 'For business section' where we will explain all the options we provide for corporate clients.
7. Social media links.
8. There needs to be a menu with buttons that leads to the all sections described in the previous points.

For now, we need a design for our front page. In the second phase, when we have picked our winner, we may ask the winner to design the page(s) for our request workflow as well.

EDIT:
Finally, we have a very specific order in mind for the different segments of our website. We would like you to add some more segments that were not in our original brief as well:

1. Top header with order/request button. (should instantly make clear our main USP, we do repairs on location)
2. Our process
3. Our unique selling points / why choose us
4. The kind of repairs we do (broken screens, broken batteries, water damage, broken camera's, no sound etc.)
5. A 'meet our team' section, where we introduce some of our engineers
6. A 'contact us for any questions' section/
7. Testimonials/user reviews
8. A section where we show key performance indicators
9. 'For businesses' sections
10.'Subscribe for newsletter' field
11. Social media buttons

Industry/Entity Type

It Service

Number of Pages Required

1 page

Font styles to use
Sans Serif

Requirements
Must have
• a main/front page, design only
• custom icons/images for banners, adverts online and in print (high res)
Nice to have
• Storytelling in our design.
• Design that fits with our brand new logo.
• Elements like icons to have a flat design.
• Keep in mind that the website will need to be responsive when designing! (Ideally provide an example of the mobile design as well)
• Create a fun and trustworthy feeling.

```html
<!DOCTYPE html>
<html lang="en">
<head>
<meta charset="utf-8">
<title>Handset Haven — Mobile Repair On Location</title>
<link href="https://fonts.googleapis.com/css2?family=Barlow:wght@400;500;600;700&family=Open+Sans:wght@300;400&display=swap" rel="stylesheet">
<style>
  :root{
    --orange:#e8591f;
    --orange-deep:#c94414;
    --lavender:#a7a6d3;
    --lavender-bg:#bcbadd;
    --ink:#2b2b2b;
    --text:#444;
    --muted:#8a8a8a;
    --line:#d8d8d8;
    --paper:#ffffff;
    --soft:#f7f7f7;
    --black:#0c0c0c;
  }
  *{box-sizing:border-box;margin:0;padding:0}
  html,body{width:1200px;height:3600px;overflow:hidden}
  body{position:relative;background:var(--paper);font-family:'Barlow',Arial,sans-serif;color:var(--ink)}
  .abs{position:absolute}

  /* Header */
  .site-header{left:0;top:0;width:1200px;height:115px;background:var(--paper)}
  .brand{left:142px;top:28px;display:flex;align-items:center;gap:12px}
  .brand-dot{width:46px;height:46px;border-radius:50%;background:var(--orange)}
  .brand-name{font-weight:700;font-size:30px;line-height:27px;color:var(--ink);text-transform:uppercase}
  .search{left:326px;top:41px;width:351px;height:42px;border:2px solid #dcdcdc;background:#fff}
  .search span{position:absolute;left:14px;top:11px;font-size:13px;color:#bbb}
  .search-btn{position:absolute;right:4px;top:4px;width:38px;height:30px;background:var(--lavender)}
  .utility{right:149px;top:12px;font-size:11px;font-weight:500;color:#666;letter-spacing:.4px}
  .main-nav{left:703px;top:52px;display:flex;font-size:15px;font-weight:600}
  .main-nav a{text-decoration:none;color:var(--ink);margin-right:30px}
  .main-nav a.active{color:var(--orange)}

  /* Hero */
  .hero{left:0;top:115px;width:1200px;height:499px;background:linear-gradient(110deg,#d8521d 0%,#e8672c 45%,#c9561f 70%,#b54817 100%)}
  .hero-photo{left:0;top:0;width:1200px;height:499px;background:radial-gradient(ellipse at 75% 40%,rgba(255,160,110,.35),transparent 60%)}
  .hero-title{left:154px;top:135px;width:420px;color:#fff;font-weight:700;font-size:44px;line-height:42px;text-transform:uppercase}
  .hero-sub{left:154px;top:294px;width:330px;color:#fff;font-weight:600;font-size:24px;line-height:29px;text-transform:uppercase}
  .btn-outline{display:flex;align-items:center;justify-content:center;border:1.5px solid #fff;color:#fff;font-weight:600;font-size:14px;letter-spacing:.5px;text-transform:uppercase}
  .hero-cta{left:154px;top:396px;width:230px;height:43px}
  .device-photo{left:720px;top:46px;width:199px;height:405px;border-radius:28px;background:linear-gradient(160deg,#f7f7f7 0%,#e4e4e4 100%)}

  /* Who we are */
  .who-photo{left:0;top:614px;width:552px;height:461px;background:linear-gradient(135deg,#c99a6a 0%,#8e7a6a 40%,#5f6e86 70%,#3e4a5c 100%)}
  .who-title{left:576px;top:668px;font-size:48px;font-weight:700;color:var(--ink);text-transform:uppercase}
  .who-text{left:576px;top:776px;width:520px;font-family:'Open Sans',Arial,sans-serif;font-size:14.5px;line-height:26px;color:var(--text)}
  .btn-dark-outline{display:flex;align-items:center;justify-content:center;border:1.5px solid var(--ink);font-weight:600;font-size:14px;color:var(--ink);text-transform:uppercase}
  .who-cta{left:576px;top:977px;width:120px;height:43px}

  /* Process */
  .process{left:0;top:1075px;width:1200px;height:1097px;background:var(--soft)}
  .section-title{width:1200px;text-align:center;font-size:46px;font-weight:700;color:var(--ink);text-transform:uppercase}
  .process-title{left:0;top:1192px}
  .process-map{left:0;top:1075px;width:1200px;height:1097px}
  .step-num{font-family:'Barlow',Arial,sans-serif;font-size:52px;font-weight:500;fill:var(--lavender)}
  .step-label{font-family:'Barlow',Arial,sans-serif;font-size:16px;font-weight:700;fill:var(--ink)}

  /* Promo cards */
  .promo{width:444px;height:295px;top:2242px;overflow:hidden}
  .promo-pricing{left:142px;background:linear-gradient(120deg,#e27a4c,#d86a3a 55%,#b8552b)}
  .promo-speed{left:610px;background:linear-gradient(120deg,#3a3a3e,#555056 50%,#2a2a2e)}
  .promo h3{position:absolute;left:38px;top:46px;width:330px;color:#fff;font-size:40px;line-height:48px;font-weight:700;text-transform:uppercase}
  .promo-speed h3{width:300px}
  .promo .btn-outline{position:absolute;left:40px;top:216px;width:180px;height:50px;font-size:16px}

  /* Testimonial */
  .testimonials{left:0;top:2597px;width:1200px;height:494px;background:var(--lavender-bg)}
  .quote-head{left:0;top:2710px;width:1200px;display:flex;justify-content:center;align-items:center;gap:14px;color:#fff;font-size:37px;font-weight:700;text-transform:uppercase}
  .quote-mark{width:74px;height:56px;display:block}
  .quote-body{left:220px;top:2814px;width:760px;text-align:center;font-family:'Open Sans',Arial,sans-serif;font-weight:300;font-size:19px;line-height:30px;color:#eeeef8}
  .reviewer{left:484px;top:2934px;display:flex;align-items:center;gap:14px}
  .avatar{width:64px;height:64px;border-radius:50%;background:linear-gradient(160deg,#e7d3c4,#a98d7d);border:3px solid #fff}
  .reviewer-name{color:#fff;font-weight:700;font-size:19px}
  .reviewer-co{color:var(--orange);font-weight:600;font-size:13px}

  /* Newsletter */
  .newsletter{left:142px;top:3156px;width:912px;height:79px;background:var(--black)}
  .newsletter-label{position:absolute;left:64px;top:17px;color:#fff;font-weight:600;font-size:13px;line-height:16px;text-transform:uppercase}
  .newsletter-label strong{display:block;font-size:23px;line-height:26px;font-weight:700}
  .newsletter-input{position:absolute;left:254px;top:18px;width:508px;height:42px;border:1.5px solid #555;color:#aaa;font-size:12px;padding:13px 18px;text-transform:uppercase;letter-spacing:.4px}
  .newsletter-btn{position:absolute;left:779px;top:18px;width:114px;height:42px;background:var(--orange);color:#fff;font-weight:700;font-size:14px;display:flex;align-items:center;justify-content:center;text-transform:uppercase}

  /* Footer */
  .footer-brand{left:142px;top:3290px}
  .footer-col{top:3296px}
  .footer-col h4{color:var(--orange);font-size:15px;font-weight:700;text-transform:uppercase;margin-bottom:16px}
  .footer-col li{list-style:none;font-size:12.5px;font-weight:600;color:var(--ink);line-height:25px;text-transform:uppercase}
  .col-quick{left:360px}.col-other{left:610px}.col-orders{left:845px}
  .footer-bottom{left:0;top:3530px;width:1200px;height:70px;border-top:1px solid #e6e6e6}
  .copyright{position:absolute;left:142px;top:26px;font-size:12px;font-weight:700;color:var(--ink)}
  .social{position:absolute;left:856px;top:22px;display:flex;align-items:center;gap:10px;font-size:12px;font-weight:700}
  .social i{display:block;width:12px;height:12px;border-radius:50%;background:var(--ink)}
  .social i.hot{background:var(--orange)}
  .lang{position:absolute;left:1160px;top:26px;font-size:12px;font-weight:700}
</style>
</head>
<body>

<header class="site-header abs">
  <div class="brand abs">
    <div class="brand-dot"></div>
    <div class="brand-name">Handset<br>Haven</div>
  </div>
  <div class="search abs"><span>Search...</span><div class="search-btn"></div></div>
  <div class="utility abs">CREDIT CARDS &nbsp;|&nbsp; ORDER STATUS &nbsp;|&nbsp; STORE LOCATOR</div>
  <nav class="main-nav abs">
    <a class="active" href="#">HOME</a>
    <a href="#">WHO WE ARE</a>
    <a href="#">PROCESS</a>
    <a href="#">CONTACT US</a>
  </nav>
</header>

<section class="hero abs">
  <div class="hero-photo abs" role="img" aria-label="Warm orange-toned photo of a workbench with repair tools"></div>
  <h1 class="hero-title abs">Professional service on location.</h1>
  <p class="hero-sub abs">Don't ship to us we will come to you!</p>
  <a class="btn-outline hero-cta abs">Get started today</a>
  <div class="device-photo abs" role="img" aria-label="Mockup of a white smartphone showing the brand on its screen"></div>
</section>

<section class="who">
  <div class="who-photo abs" role="img" aria-label="Photo of a young man in a hoodie looking at his smartphone"></div>
  <h2 class="who-title abs">Who we are ?</h2>
  <p class="who-text abs">Our company is based in Rotterdam, the Netherlands. We provide different services for &nbsp;all kinds of electronic devices. The kind of services we provide are, among other things,installations of hardware and software and the repair of broken or malfunctioning devices.We are starting a new service that offers mobile device repairs on location, be it at the home of our customers, their office, or any other place.</p>
  <a class="btn-dark-outline who-cta abs">Read more</a>
</section>

<section class="process abs"></section>
<h2 class="section-title process-title abs">Process</h2>
<svg class="process-map abs" viewBox="0 0 1200 1097">
  <defs>
    <marker id="chev" viewBox="0 0 10 10" refX="6" refY="5" markerWidth="9" markerHeight="9" orient="auto">
      <path d="M1 1 L7 5 L1 9" fill="none" stroke="#bdbdbd" stroke-width="1.4"/>
    </marker>
  </defs>
  <g fill="none" stroke="#c4c4c4" stroke-width="2" marker-end="url(#chev)">
    <path d="M392 418 Q412 370 455 348"/>
    <path d="M735 378 Q780 392 808 440"/>
    <path d="M880 700 Q875 740 848 768"/>
    <path d="M640 900 Q598 912 552 900"/>
    <path d="M382 772 Q360 740 360 700"/>
  </g>
  <g fill="#fff" stroke="#e8591f" stroke-width="5">
    <circle cx="598" cy="358" r="106"/>
    <circle cx="866" cy="571" r="106"/>
    <circle cx="754" cy="871" r="106"/>
    <circle cx="422" cy="871" r="106"/>
    <circle cx="338" cy="535" r="106"/>
  </g>
  <text class="step-num" x="598" y="348" text-anchor="middle">1</text>
  <text class="step-label" x="598" y="381" text-anchor="middle">CHOOSE YOUR</text>
  <text class="step-label" x="598" y="400" text-anchor="middle">DEVICE &amp;</text>
  <text class="step-label" x="598" y="419" text-anchor="middle">REPAIR JOB</text>

  <text class="step-num" x="866" y="571" text-anchor="middle">2</text>
  <text class="step-label" x="866" y="600" text-anchor="middle">PLACE</text>
  <text class="step-label" x="866" y="619" text-anchor="middle">THE ORDER</text>

  <text class="step-num" x="754" y="871" text-anchor="middle">3</text>
  <text class="step-label" x="754" y="907" text-anchor="middle" style="font-size:14px">GET A CALLBACK</text>
  <text class="step-label" x="754" y="926" text-anchor="middle" style="font-size:14px">WITHIN THE HOUR</text>

  <text class="step-num" x="422" y="871" text-anchor="middle">4</text>
  <text class="step-label" x="422" y="907" text-anchor="middle" style="font-size:14px">SET DATE AND</text>
  <text class="step-label" x="422" y="926" text-anchor="middle" style="font-size:14px">LOCATION</text>

  <text class="step-num" x="338" y="535" text-anchor="middle">5</text>
  <text class="step-label" x="338" y="565" text-anchor="middle">WE WILL</text>
  <text class="step-label" x="338" y="584" text-anchor="middle">COME TO YOU</text>

  <circle cx="600" cy="610" r="42" fill="#e8591f"/>
  <text x="600" y="684" text-anchor="middle" font-family="Barlow,Arial,sans-serif" font-weight="700" font-size="22" fill="#2b2b2b">HANDSET HAVEN</text>
</svg>

<section>
  <article class="promo promo-pricing abs" role="img" aria-label="Orange-tinted photo of hands holding a phone at a desk">
    <h3>Clear pricing upfront. No hidden cost.</h3>
    <a class="btn-outline">Order now</a>
  </article>
  <article class="promo promo-speed abs" role="img" aria-label="Dark photo of a person using a phone beside a laptop">
    <h3>Next business-day repair.</h3>
    <a class="btn-outline">Order now</a>
  </article>
</section>

<section class="testimonials abs"></section>
<h2 class="quote-head abs">
  <svg class="quote-mark" viewBox="0 0 74 56" aria-hidden="true">
    <g fill="#fff">
      <circle cx="17" cy="38" r="15"/>
      <path d="M4 36 Q6 10 30 2 L32 8 Q16 16 16 30 Z"/>
      <circle cx="55" cy="38" r="15"/>
      <path d="M42 36 Q44 10 68 2 L70 8 Q54 16 54 30 Z"/>
    </g>
  </svg>
  What our customers have to say
</h2>
<p class="quote-body abs">Sed ut perspiciatis unde omnis iste natus error sit voluptatem accusantium doloremque laudantium, totam rem aperiam, eaque ipsa quae ab illo inventore veritatis et quasi architecto beatae vitae dicta sunt explicabo.</p>
<div class="reviewer abs">
  <div class="avatar" role="img" aria-label="Customer portrait photo"></div>
  <div>
    <div class="reviewer-name">Daniel Voss</div>
    <div class="reviewer-co">Company Name</div>
  </div>
</div>

<section class="newsletter abs">
  <div class="newsletter-label">Get latest updates from<strong>Handset Haven</strong></div>
  <div class="newsletter-input">Enter your e-mail address</div>
  <div class="newsletter-btn">Subscribe !</div>
</section>

<footer>
  <div class="brand footer-brand abs">
    <div class="brand-dot"></div>
    <div class="brand-name">Handset<br>Haven</div>
  </div>
  <div class="footer-col col-quick abs">
    <h4>Quick links</h4>
    <ul><li>Home</li><li>Who we are</li><li>Process</li><li>Contact us</li></ul>
  </div>
  <div class="footer-col col-other abs">
    <h4>Other links</h4>
    <ul><li>Terms of service</li><li>Privacy policy</li><li>Help</li><li>Disclaimer</li></ul>
  </div>
  <div class="footer-col col-orders abs">
    <h4>Orders &amp; returns</h4>
    <ul><li>Order status</li><li>Shipping</li><li>Delivery &amp; store pickup</li><li>Return &amp; exchange</li><li>More orders</li><li>Returns</li><li>Help</li></ul>
  </div>
  <div class="footer-bottom abs">
    <div class="copyright">© 2017 Company Name &nbsp;| All Rights Reserved</div>
    <div class="social">Connect With Us <i class="hot"></i><i></i><i></i><i></i><i></i></div>
    <div class="lang">CS</div>
  </div>
</footer>

</body>
</html>
```